Packaging design for a reclosable bag for our product

We have a logo, and we need to put it on packaging for our product and while we want the look to be simple, we want it to follow good design principles and also contain spaces for other product descriptions.

There will be 5 sizes at launch so I'd like 5 variations, one for each size.

I've included a few mockups of the type of bag that I made but they are all just rough ideas that I had.

I want the brand to look scientific and methodical and even a bit quirky, as in "wow this is a serious product but also a bit unusual."

```html
<!DOCTYPE html>
<html lang="en">
<head>
<meta charset="utf-8">
<title>Bias Lighting – NV4 Pouch Front</title>
<link href="https://fonts.googleapis.com/css2?family=Bebas+Neue&family=Lato:wght@400&display=swap" rel="stylesheet">
<style>
  :root {
    --backdrop: #c6c6c6;
    --pouch: #141414;
    --pouch-edge: #0b0b0b;
    --zip: #222222;
    --white: #ffffff;
    --ink: #1d1d1d;
    --band-fade: #9a9a9a;
  }
  * { margin: 0; padding: 0; box-sizing: border-box; }
  html, body {
    width: 1200px; height: 1200px; overflow: hidden;
    background: var(--backdrop);
  }
  .canvas { position: relative; width: 1200px; height: 1200px; }
  .pouch-front {
    position: absolute; left: 160px; top: 26px;
    width: 880px; height: 1148px;
    background: linear-gradient(180deg, var(--pouch-edge) 0%, var(--pouch) 20%, var(--pouch) 100%);
    overflow: hidden;
  }
  .zip-seal {
    position: absolute; left: 0; right: 0; top: 140px; height: 22px;
    background: var(--zip);
    border-top: 1px solid #2c2c2c; border-bottom: 1px solid #0a0a0a;
  }
  .category-band {
    position: absolute; left: 0; right: 0; top: 266px; height: 100px;
    background: linear-gradient(90deg, #3a3a3a 0%, var(--band-fade) 12%, var(--white) 26%, var(--white) 74%, var(--band-fade) 88%, #3a3a3a 100%);
    display: flex; align-items: center; justify-content: center;
  }
  .category-band h1 {
    font-family: "Bebas Neue", sans-serif; font-weight: 400;
    font-size: 82px; line-height: 1; letter-spacing: 1px;
    color: var(--ink); padding-top: 6px;
  }
  .product-name {
    position: absolute; left: 0; right: 0; top: 520px;
    display: flex; align-items: center; justify-content: center; gap: 28px;
  }
  .product-name .mark-square {
    width: 40px; height: 40px; background: var(--white);
  }
  .product-name span {
    font-family: "Bebas Neue", sans-serif; font-weight: 400;
    font-size: 260px; line-height: 1; color: var(--white);
  }
  .feature-row {
    position: absolute; left: 0; right: 0; top: 948px;
    display: flex; justify-content: center; align-items: stretch;
  }
  .feature {
    display: flex; flex-direction: column; align-items: center;
    padding: 0 14px; gap: 4px;
  }
  .feature + .feature { border-left: 2px solid var(--white); }
  .feature svg { width: 64px; height: 64px; }
  .feature p {
    font-family: "Lato", sans-serif; font-size: 16px;
    color: var(--white); white-space: nowrap;
  }
</style>
</head>
<body>
<main class="canvas">
  <section class="pouch-front">
    <div class="zip-seal"></div>

    <div class="category-band">
      <h1>Bias Lighting</h1>
    </div>

    <div class="product-name">
      <div class="mark-square"></div>
      <span>NV4</span>
    </div>

    <ul class="feature-row">
      <li class="feature">
        <svg viewBox="0 0 64 64" fill="none" stroke="#fff" stroke-width="2">
          <rect x="10" y="26" width="44" height="12" />
          <rect x="14" y="29" width="36" height="6" fill="#fff" />
          <g stroke-width="1.6">
            <line x1="14" y1="22" x2="12" y2="16"/><line x1="22" y1="22" x2="21" y2="16"/><line x1="32" y1="22" x2="32" y2="16"/><line x1="42" y1="22" x2="43" y2="16"/><line x1="50" y1="22" x2="52" y2="16"/>
            <line x1="14" y1="42" x2="12" y2="48"/><line x1="22" y1="42" x2="21" y2="48"/><line x1="32" y1="42" x2="32" y2="48"/><line x1="42" y1="42" x2="43" y2="48"/><line x1="50" y1="42" x2="52" y2="48"/>
          </g>
        </svg>
        <p>6500K White</p>
      </li>
      <li class="feature">
        <svg viewBox="0 0 64 64" fill="none" stroke="#fff" stroke-width="1.6">
          <circle cx="32" cy="32" r="12"/>
          <g>
            <line x1="32" y1="12" x2="32" y2="6"/><line x1="32" y1="52" x2="32" y2="58"/>
            <line x1="12" y1="32" x2="6" y2="32"/><line x1="52" y1="32" x2="58" y2="32"/>
            <line x1="18" y1="18" x2="14" y2="14"/><line x1="46" y1="46" x2="50" y2="50"/>
            <line x1="46" y1="18" x2="50" y2="14"/><line x1="18" y1="46" x2="14" y2="50"/>
          </g>
          <text x="32" y="35.5" font-family="Lato, sans-serif" font-size="9" fill="#fff" stroke="none" text-anchor="middle">D65</text>
        </svg>
        <p>Simulated</p>
      </li>
      <li class="feature">
        <svg viewBox="0 0 64 64">
          <circle cx="32" cy="32" r="24" fill="none" stroke="#fff" stroke-width="8" stroke-dasharray="6 3"/>
          <circle cx="32" cy="32" r="16" fill="#fff"/>
          <text x="32" y="36.5" font-family="Lato, sans-serif" font-size="12" fill="#141414" text-anchor="middle">CRI</text>
        </svg>
        <p>90+</p>
      </li>
      <li class="feature">
        <svg viewBox="0 0 64 64" fill="none" stroke="#fff" stroke-width="1.8">
          <circle cx="32" cy="30" r="24"/><circle cx="32" cy="30" r="17"/><circle cx="32" cy="30" r="10"/><circle cx="32" cy="30" r="4"/>
          <line x1="4" y1="58" x2="60" y2="58"/>
        </svg>
        <p>Cable Length 5m</p>
      </li>
      <li class="feature">
        <svg viewBox="0 0 64 64" fill="none" stroke="#fff" stroke-width="2.2">
          <path d="M10 20 a32 32 0 0 1 44 0"/><path d="M17 27 a22 22 0 0 1 30 0"/><path d="M24 34 a12 12 0 0 1 16 0"/>
          <rect x="27" y="40" width="10" height="20" rx="2" fill="#fff" stroke="none"/>
        </svg>
        <p>Wireless Control</p>
      </li>
    </ul>
  </section>
</main>
</body>
</html>
```